Bry7Legal Letterhead

Need a new letterhead for my law firm.
IDENTIFYING INFORMATION BELOW:
Anselmo R Quintara III
Attorney at Law
Address: 2847 Larkspur Blvd, Ste 300, Dallas, TX 75204
Phone: 877-482-6017
Fax: 469-738-1452
Email: bry@bry7legal.example
Website: www.bry7legal.example

Colors
0054AA
0677BA
7BADD7
CADEEF
E8F1F8

Requirements
Must have
• Logo needs to be on the letterhead, along with identifying information which is included in the project description.

```html
<!DOCTYPE html>
<html lang="en">
<head>
<meta charset="utf-8">
<title>Bry7Legal Letterhead</title>
<link rel="stylesheet" href="https://fonts.googleapis.com/css2?family=Lato:wght@400;700;900&family=Open+Sans:wght@400;600&display=swap">
<style>
  :root {
    --navy: #0054AA;
    --blue: #0677BA;
    --sky: #7BADD7;
    --pale: #CADEEF;
    --mist: #E8F1F8;
    --ink: #3a3a3a;
    --dark: #111;
    --backdrop: #e6e8ea;
    --paper: #ffffff;
  }
  * { margin: 0; padding: 0; box-sizing: border-box; }
  html, body { width: 1040px; height: 1200px; overflow: hidden; background: var(--backdrop); }
  .letterhead {
    position: absolute; left: 53px; top: 0;
    width: 934px; height: 1200px;
    background: var(--paper);
    font-family: "Open Sans", sans-serif;
    color: var(--ink);
    overflow: hidden;
  }
  .brand {
    position: absolute; left: 592px; top: 44px; width: 236px;
    font-family: "Lato", sans-serif; font-weight: 900;
    font-size: 34px; color: var(--dark); letter-spacing: 0.5px;
    text-align: center; line-height: 1;
  }
  .letter-body { position: absolute; left: 88px; width: 754px; font-size: 14.5px; }
  .meta { top: 222px; line-height: 18px; }
  .meta .date { margin-bottom: 18px; }
  .salutation { top: 363px; }
  .paragraph { line-height: 27px; text-align: justify; }
  .p1 { top: 415px; }
  .p2 { top: 576px; }
  .p3 { top: 684px; }
  .closing { top: 820px; }
  .signature {
    position: absolute; left: 88px; top: 858px; width: 214px; height: 30px;
    background: linear-gradient(90deg, var(--mist), #f3f3f3);
  }
  .signer { position: absolute; left: 88px; top: 898px; font-size: 18.5px; font-weight: 600; color: var(--dark); }
  .signer-title { position: absolute; left: 88px; top: 930px; font-size: 14.5px; }

  .footer { font-family: "Lato", sans-serif; }
  .attorney-name { position: absolute; left: 86px; top: 1071px; font-size: 21px; font-weight: 700; color: var(--blue); }
  .attorney-role { position: absolute; left: 86px; top: 1096px; font-size: 17px; color: var(--dark); }
  .contact-band {
    position: absolute; left: 0; top: 1131px; width: 765px; height: 39px;
    background: linear-gradient(180deg, var(--sky) 0%, var(--blue) 35%, var(--navy) 100%);
    color: #fff; font-size: 15px; line-height: 39px; padding-left: 86px; white-space: nowrap;
  }
  .contact-band b { font-weight: 700; }
  .contact-band .sep { margin: 0 5px; }
  .address { position: absolute; left: 86px; top: 1175px; font-size: 17.5px; color: var(--dark); }
  .corner-block {
    position: absolute; left: 776px; top: 1072px; width: 158px; height: 128px;
    background: linear-gradient(135deg, var(--sky), var(--blue) 45%, var(--navy));
  }
</style>
</head>
<body>
<main class="letterhead">
  <header class="brand">Bry7Legal</header>

  <section class="letter-body meta">
    <p class="date">Issuing Date: May 5, 2018</p>
    <p>Name Of Employee Mr. XYZABC</p>
    <p>Address of Employee</p>
    <p>Address Line 2 etc..</p>
  </section>

  <p class="letter-body salutation">Dear Mr.XYZABC</p>

  <p class="letter-body paragraph p1">Lorem Ipsum has been the industry's standard dummy text ever since the 1500s, when an unknown printer took a galley of type and scrambled it to make a type specimen book. It has survived not only five centuries, but also the leap into electronic typesetting, remaining essentially unchanged. It was popularised in the 1960s with the release of Letraset sheets containing Lorem Ipsum passages, and more recently with desktop publishing software like Aldus PageMaker including versions of Lorem Ipsum.</p>

  <p class="letter-body paragraph p2">Lorem Ipsum is simply dummy text of the printing and typesetting industry. Lorem Ipsum has been the industry's standard dummy text ever since the 1500s, when an unknown printer took a galley of type and scrambled it to make a type specimen book.</p>

  <p class="letter-body paragraph p3">It has survived not only five centuries, but also the leap into electronic typesetting, remaining essentially unchanged. It was popularised in the 1960s with the release of Letraset sheets containing Lorem IpsumIpsum passages.</p>

  <p class="letter-body closing">Yours Sincerely</p>
  <div class="signature" role="img" aria-label="Handwritten signature of Marcus Delaney"></div>
  <p class="signer">Marcus Delaney</p>
  <p class="signer-title">Managing Director</p>

  <footer class="footer">
    <p class="attorney-name">Anselmo R Quintara III</p>
    <p class="attorney-role">Attorney at Law</p>
    <div class="contact-band">
      <b>P:</b> 877-482-6017<span class="sep">|</span><b>F:</b> 469-738-1452<span class="sep">|</span><b>E:</b> bry@bry7legal.example<span class="sep">|</span><b>W:</b> www.bry7legal.example
    </div>
    <p class="address">2847 Larkspur Blvd, Ste 300, Dallas, TX 75204</p>
    <div class="corner-block"></div>
  </footer>
</main>
</body>
</html>
```